Packaging and logo design for washcloths

We are a company manufacturing towels and washcloths for babies.We are planning to get into e-commerce business with washcloths for babies made out of 100% Rayon made from Bamboo.We would like to see a logo design that symbolizes the perfection of the nature and a packaging design that gives mothers the feeling of cleanliness,pureness, softness and eco-friendliness. The packaging will include 6 items, each washcloth is 10x10 inches. The details will be discussed with the designer.
Updates

Looking for a clean and neat design that will attract the buyers which will also emphasize the fact that it is made out of highest quality rayon from bamboo that don’t irritate sensitive and delicate skin. I am planning to outsource more work (website,flyers, pictures and social media related stuff) to the designers who does the best job for this packaging project .

Target Market(s)

E-commerce customers, mothers,

Colors

Designer to choose colors to be used in the design.

Requirements
Must have
• clean and stylish look that should emphasize the fact that the product is 100% organic bamboo, eco-friendly,premium ultra soft, perfect for delicate and sensitive skin and 100% natural.Kraft paper packaging might be more suitable for an eco-friendly, bamboo based product.
Nice to have
• Packaging dimensions of our first competitors is 8.3 x 5.6 x 1.4 inches and the second one is 8.2 x 5.8 x 1.5 inches therefore; the final product should be designed according to these dimensions keeping in mind that each box will have 6 towels in it.

```html
<!DOCTYPE html>
<html lang="en">
<head>
<meta charset="utf-8">
<title>Pure Bamboo Washcloth – Front Panel</title>
<link rel="stylesheet" href="https://fonts.googleapis.com/css2?family=Antonio:wght@300&family=Roboto:wght@400;500;700&display=swap">
<style>
  :root {
    --stage: #e9e9ea;
    --white: #ffffff;
    --green: #7cc142;
    --green-light: #b9dc8a;
    --green-dark: #1f5a2a;
    --blue: #1e9be0;
    --blue-deep: #0a7fcf;
    --grey-icon: #8a8a8a;
    --grey-text: #4a4a4a;
  }
  * { box-sizing: border-box; margin: 0; padding: 0; }
  html, body { width: 1200px; height: 582px; overflow: hidden; background: var(--stage); }
  .front-panel {
    position: absolute; left: 178px; top: 8px;
    width: 844px; height: 566px;
    background: var(--white);
    overflow: hidden;
    font-family: "Roboto", sans-serif;
  }
  .panel-art { position: absolute; inset: 0; width: 100%; height: 100%; }
  .bamboo-illustration {
    position: absolute; left: 33px; top: 57px; width: 279px; height: 434px;
    border-radius: 40px;
    background: radial-gradient(ellipse at 50% 45%, #dff0c9 0%, #eef7e3 60%, rgba(255,255,255,0) 100%);
  }
  .product-window {
    position: absolute; left: 23px; top: 186px; width: 268px; height: 274px;
    border-radius: 90px 30px 90px 30px;
    transform: rotate(-8deg);
    background: linear-gradient(180deg, #e6c9d6 0%, #b49ac9 28%, #a5c4e6 52%, #c9d7ee 68%, #efc6cf 100%);
    box-shadow: 0 2px 6px rgba(0,0,0,.25);
  }
  .brand-name {
    position: absolute; left: 470px; top: 122px;
    display: flex; align-items: center; gap: 10px;
    font-weight: 700; font-size: 32px; color: var(--blue);
    letter-spacing: .5px; white-space: nowrap;
  }
  .brand-name .brand-dot { width: 20px; height: 20px; border-radius: 50%; background: var(--green); }
  .product-title {
    position: absolute; left: 432px; top: 206px; width: 324px;
    font-family: "Antonio", sans-serif; font-weight: 300;
    font-size: 58px; line-height: 1; color: var(--green-dark);
    text-align: center; white-space: nowrap;
  }
  .product-subtitle {
    position: absolute; left: 451px; top: 276px; width: 286px; height: 29px;
    background: var(--blue); color: var(--white);
    font-weight: 500; font-size: 20px; line-height: 29px; text-align: center;
    white-space: nowrap;
  }
  .feature-list {
    position: absolute; left: 455px; top: 330px; width: 280px;
    display: flex; list-style: none;
    border-bottom: 1px solid var(--green);
    padding-bottom: 6px;
  }
  .feature {
    flex: 1; text-align: center;
    font-size: 12px; font-weight: 500; color: var(--grey-text);
    white-space: nowrap;
  }
  .feature + .feature { border-left: 1px solid var(--grey-icon); }
  .feature svg { display: block; margin: 0 auto 6px; width: 22px; height: 22px; }
  .website {
    position: absolute; left: 445px; top: 394px; width: 300px;
    text-align: center; font-weight: 700; font-size: 13px;
    letter-spacing: 2.6px; color: var(--blue); white-space: nowrap;
  }
  .count-badge { position: absolute; left: 658px; top: 420px; width: 134px; height: 134px; }
  .badge-text {
    position: absolute; left: 658px; top: 420px; width: 134px; height: 134px;
    color: var(--white); text-align: center; transform: rotate(-12deg);
  }
  .badge-text .badge-count { position: absolute; left: 30px; top: 24px; font-size: 42px; font-weight: 700; line-height: 1; }
  .badge-text .badge-label-top { position: absolute; left: 58px; top: 32px; font-size: 13px; }
  .badge-text .badge-label { position: absolute; left: 17px; top: 58px; width: 100px; font-size: 20px; font-weight: 700; }
  .badge-text .badge-size { position: absolute; left: 20px; top: 90px; width: 94px; font-size: 9px; font-weight: 500; white-space: nowrap; }
  .care-note {
    position: absolute; left: 29px; top: 514px; width: 530px;
    font-size: 11.5px; line-height: 1.35; color: var(--white);
  }
</style>
</head>
<body>
<main class="front-panel">
  <svg class="panel-art" viewBox="0 0 817 548" preserveAspectRatio="none" aria-hidden="true">
    <path d="M0 0 H817 V62 C700 22 560 22 420 40 C260 60 120 42 0 36 Z" fill="var(--green)"/>
    <path d="M430 0 H817 V76 C740 40 630 28 520 34 C480 30 450 14 430 0 Z" fill="var(--green-light)"/>
    <path d="M0 488 C400 488 700 470 817 340 V548 H0 Z" fill="var(--blue)"/>
    <path d="M0 508 C400 508 700 500 817 392 V548 H0 Z" fill="var(--blue-deep)"/>
    <path d="M380 548 C560 530 720 490 817 400 V548 Z" fill="var(--green)"/>
    <path d="M290 548 C520 524 690 480 817 418" stroke="var(--white)" stroke-width="2" fill="none"/>
    <path d="M0 481 C400 481 700 462 817 331" stroke="var(--white)" stroke-width="1.5" fill="none"/>
  </svg>

  <div class="bamboo-illustration" role="img" aria-label="Line drawing of bamboo stalks with green leaves"></div>
  <div class="product-window" role="img" aria-label="Window showing stacked pink, lilac and blue washcloths"></div>

  <div class="brand-name"><span class="brand-dot"></span>Bambino Soft</div>
  <h1 class="product-title">PURE BAMBOO</h1>
  <p class="product-subtitle">100% RAYON WASHCLOTH</p>

  <ul class="feature-list">
    <li class="feature">
      <svg viewBox="0 0 24 24"><rect x="3" y="4" width="8" height="16" rx="4" fill="var(--grey-icon)"/><rect x="13" y="4" width="8" height="16" rx="4" fill="var(--grey-icon)" transform="rotate(20 17 12)"/></svg>
      Hypoallergenic
    </li>
    <li class="feature">
      <svg viewBox="0 0 24 24"><circle cx="12" cy="12" r="6" fill="var(--grey-icon)"/><g stroke="var(--grey-icon)" stroke-width="2"><line x1="12" y1="1" x2="12" y2="23"/><line x1="1" y1="12" x2="23" y2="12"/><line x1="4" y1="4" x2="20" y2="20"/><line x1="20" y1="4" x2="4" y2="20"/></g></svg>
      Antibacterial
    </li>
    <li class="feature">
      <svg viewBox="0 0 24 24"><path d="M4 20 C4 9 11 4 21 4 C21 14 15 20 4 20 Z" fill="var(--grey-icon)"/><path d="M4 20 L14 10" stroke="var(--white)" stroke-width="1.5"/></svg>
      Ecofriendly
    </li>
  </ul>
  <p class="website">www.bambinosoft.com</p>

  <svg class="count-badge" viewBox="0 0 100 100" aria-hidden="true">
    <polygon points="50,2 58,8 68,5 73,14 83,14 85,24 94,28 92,38 99,45 94,53 98,62 90,68 91,78 82,81 79,91 69,90 62,98 53,93 44,98 37,90 27,92 22,83 12,81 12,71 4,65 8,56 2,48 8,41 5,31 14,26 15,16 25,14 30,5 40,7" fill="var(--green)"/>
    <circle cx="50" cy="50" r="40" fill="none" stroke="var(--white)" stroke-width="1.8"/>
  </svg>
  <div class="badge-text">
    <span class="badge-count">6</span>
    <span class="badge-label-top">premium</span>
    <span class="badge-label">Washcloth</span>
    <span class="badge-size">10X10 INCHES</span>
  </div>

  <p class="care-note">The hypoallergenic, soft, anti-bacterial fibres mean that even sensitive skin or eczema will not be irritated and your baby enjoys bathtime without getting hurt.</p>
</main>
</body>
</html>
```